Business Card for Lantern Reach

Please design a Modern Business card for a Online Marketing Company

Website: http://www.lanternreach-example.com.au

Please do NOT include physical address in design.

```html
<!DOCTYPE html>
<html lang="en">
<head>
<meta charset="utf-8">
<title>Lantern Reach – Business Card</title>
<link rel="stylesheet" href="https://fonts.googleapis.com/css2?family=Roboto:wght@400;700;900&family=Open+Sans:wght@400;600;700&display=swap">
<style>
  :root {
    --backdrop: #e9e6e2;
    --card-white: #ffffff;
    --brand-red: #c0111f;
    --ink: #1c1c1c;
    --rule: #9a9a9a;
    --on-red: #ffffff;
  }
  * { box-sizing: border-box; margin: 0; padding: 0; }
  html, body { width: 1200px; height: 466px; overflow: hidden; }
  body {
    background: var(--backdrop);
    position: relative;
    font-family: "Open Sans", Arial, sans-serif;
  }
  .card {
    position: absolute;
    top: 88px;
    width: 510px;
    height: 290px;
    box-shadow: 0 6px 18px rgba(0,0,0,0.25);
  }
  .card--front { left: 50px; background: var(--card-white); }
  .card--back { left: 640px; background: var(--brand-red); color: var(--on-red); }

  .brand {
    position: absolute;
    top: 36px;
    left: 118px;
    display: flex;
    align-items: center;
    gap: 12px;
  }
  .brand__mark {
    width: 40px; height: 40px;
    background: var(--brand-red);
  }
  .brand__name {
    font-family: "Roboto", Arial, sans-serif;
    font-weight: 900;
    font-size: 25px;
    color: var(--brand-red);
    letter-spacing: 0.2px;
    line-height: 1;
  }
  .brand__tagline {
    font-family: "Roboto", Arial, sans-serif;
    font-weight: 700;
    font-size: 13px;
    color: var(--ink);
    margin-top: 3px;
  }

  .person {
    position: absolute;
    top: 150px;
    left: 0; right: 0;
    text-align: center;
    color: var(--brand-red);
    font-size: 19px;
    letter-spacing: 0.8px;
  }
  .person__name { font-weight: 700; }
  .person__title { font-weight: 400; font-size: 16px; }
  .person__rule {
    width: 250px; height: 1px;
    margin: 8px auto 0;
    background: var(--rule);
  }

  .contacts {
    position: absolute;
    top: 192px;
    left: 0; right: 0;
    list-style: none;
    text-align: center;
    font-size: 14px;
    color: var(--ink);
    line-height: 23px;
    letter-spacing: 0.3px;
  }
  .contacts li { display: flex; justify-content: center; align-items: center; gap: 6px; }
  .contacts svg { width: 12px; height: 12px; fill: var(--ink); }

  .back__brand {
    position: absolute;
    top: 88px;
    left: 0; right: 0;
    text-align: center;
    font-family: "Roboto", Arial, sans-serif;
  }
  .back__name { font-weight: 900; font-size: 42px; line-height: 1; letter-spacing: 0.5px; }
  .back__tagline { font-weight: 700; font-size: 20px; margin-top: 4px; }
  .back__web {
    position: absolute;
    bottom: 48px;
    left: 0; right: 0;
    text-align: center;
    font-size: 17px;
    letter-spacing: 0.8px;
  }
</style>
</head>
<body>
  <section class="card card--front" aria-label="Business card front">
    <div class="brand">
      <div class="brand__mark"></div>
      <div>
        <div class="brand__name">LANTERN REACH</div>
        <div class="brand__tagline">Be seen online - Grow online</div>
      </div>
    </div>

    <div class="person">
      <span class="person__name">Your Name</span><span class="person__title">, Title</span>
      <div class="person__rule"></div>
    </div>

    <ul class="contacts">
      <li>
        <svg viewBox="0 0 24 24" aria-hidden="true"><path d="M6.6 10.8a15 15 0 0 0 6.6 6.6l2.2-2.2c.3-.3.7-.4 1-.2 1.1.4 2.3.6 3.6.6.6 0 1 .4 1 1V20c0 .6-.4 1-1 1A17 17 0 0 1 3 4c0-.6.4-1 1-1h3.5c.6 0 1 .4 1 1 0 1.3.2 2.5.6 3.6.1.3 0 .7-.2 1z"/></svg>
        0400 555 017
      </li>
      <li>
        <svg viewBox="0 0 24 24" aria-hidden="true"><path d="M2 5h20v14H2zm2 2v.5l8 5 8-5V7zm0 2.8V17h16V9.8l-8 5z"/></svg>
        hello@lanternreach-example.com.au
      </li>
      <li>
        <svg viewBox="0 0 24 24" aria-hidden="true"><path d="M12 2a10 10 0 1 0 0 20 10 10 0 0 0 0-20zm6.9 6h-3a15 15 0 0 0-1.3-3.9A8 8 0 0 1 18.9 8zM12 4c.8 1.2 1.5 2.5 1.9 4h-3.8c.4-1.5 1.1-2.8 1.9-4zM4.3 14a8 8 0 0 1 0-4h3.4a16 16 0 0 0 0 4zm.8 2h3a15 15 0 0 0 1.3 3.9A8 8 0 0 1 5.1 16zm3-8h-3a8 8 0 0 1 4.3-3.9C8.8 5.3 8.4 6.6 8.1 8zM12 20c-.8-1.2-1.5-2.5-1.9-4h3.8c-.4 1.5-1.1 2.8-1.9 4zm2.3-6H9.7a14 14 0 0 1 0-4h4.6a14 14 0 0 1 0 4zm.3 5.9c.6-1.200 1-2.5 1.3-3.9h3a8 8 0 0 1-4.3 3.9zm1.7-5.9a16 16 0 0 0 0-4h3.4a8 8 0 0 1 0 4z"/></svg>
        www.lanternreach-example.com.au
      </li>
    </ul>
  </section>

  <section class="card card--back" aria-label="Business card back">
    <div class="back__brand">
      <div class="back__name">LANTERN REACH</div>
      <div class="back__tagline">Be seen online - Grow online</div>
    </div>
    <div class="back__web">www.lanternreach-example.com.au</div>
  </section>
</body>
</html>
```